Willow Cradle Pregnancy and Baby Massage

I need a web design for a new business, WILLOW CRADLE PREGNANCY AND BABY MASSAGE that I am in the process of setting up in the suburbs of Perth, Western Australia. The business is owned and operated by myself and my intention is to service Pregnant Mothers and Parents of Young Babies that would benefit from massage. I would like to have a "Home Page" and pages for "About Me", "Pregnancy Massage", "Baby Massage", a Pricing Page for Pregnancy Massage Sessions, a Pricing Page for Baby Massage Sessions, and a "Contact Me" page to allow clients to either contact me with queries or book available pregnancy massage sessions on a particular day of the week. I would also like a "News" page that would include articles I have written, news about new courses and a link to my Facebook page (yet to be set up). I would like to keep the colour schemes similar to my logo design colours. I need the design to be easy to follow and to appeal to a younger audience (20's to mid 30's).
The target audience is pregnant mothers-to-be wishing to receive massage treatments, and new parents and grandparents of small babies that would like to learn how to massage their babies.
The look and feel should be modern, professional, elegant and feminine.
I need the design to be in a standard format such that I can update the content by myself ( and does not need specialised software) as the company and business progresses.

Target Market(s)

Contact Information for Business Card

Card should have rounded edges. Design should have the same "feel" as the website. Contact Details of my business address, mobile phone, email and website should be included.

Font styles to use
Script

Requirements
Must have
• Same colours as logo design. In cmyk system, the colours are: 20,60,0,0 which best result is pantone 681 and 40,40,0,0 which best result is pantone 2645. Card should include the logo design.

```html
<!DOCTYPE html>
<html lang="en">
<head>
<meta charset="utf-8">
<title>Willow Cradle Pregnancy and Baby Massage</title>
<link rel="stylesheet" href="https://fonts.googleapis.com/css2?family=Dancing+Script:wght@600&family=Arimo:wght@400&display=swap">
<style>
:root{
  --plum-deep:#3a1637;
  --plum:#5a2a57;
  --orchid:#b7679f;
  --orchid-dark:#9c4f87;
  --lavender:#8c82bb;
  --mist:#f3f1f8;
  --blush:#f7eef4;
  --ink:#222;
  --text:#555;
  --white:#fff;
}
*{margin:0;padding:0;box-sizing:border-box}
html,body{width:1200px;height:2711px;overflow:hidden}
body{background:var(--mist);font-family:"Arimo",Arial,sans-serif;color:var(--text);position:relative}
.script{font-family:"Dancing Script",cursive;font-weight:600}
.abs{position:absolute}

/* hero */
.hero{left:0;top:0;width:1200px;height:674px;background:linear-gradient(90deg,var(--plum-deep) 0%,var(--plum) 30%,#6b4768 40%,#cfc8cc 60%,#e9e6e6 100%);overflow:hidden}
.hero-photo{left:430px;top:0;width:770px;height:674px;background:radial-gradient(ellipse at 55% 45%,#8d8a8f 0%,#c9c4c6 35%,#e4e1e1 65%,#b9a39a 100%);opacity:.85}
.hero-swoop{left:0;top:0}
.brand{left:76px;top:60px;width:260px;color:var(--orchid);font-size:40px;line-height:1.05}
.brand-dot{display:inline-block;width:22px;height:22px;border-radius:50%;background:var(--orchid);margin-bottom:10px}
.nav{right:60px;top:40px;display:flex;gap:46px;list-style:none;font-size:15px}
.nav a{color:var(--orchid);text-decoration:none}
.nav a.active{color:var(--ink)}
.hero-title{left:78px;top:310px;color:var(--white);font-size:46px;line-height:1.2}
.hero-btn{left:78px;top:453px;width:240px;height:51px;border:2px solid var(--white);border-radius:4px;color:var(--white);font-size:22px;display:flex;align-items:center;justify-content:center}

/* content */
.panel{left:78px;width:1044px}
.intro{top:623px;height:367px;background:var(--white)}
.heart-photo{left:20px;top:14px;width:440px;height:340px;background:radial-gradient(ellipse at 45% 50%,#e9a48c 0%,#f2cfc3 40%,#fbf4f1 70%,var(--white) 100%)}
.bullets{list-style:none;font-size:16px;line-height:1.8}
.bullets li{position:relative;padding-left:26px;margin-bottom:10px}
.bullets li::before{content:"";position:absolute;left:0;top:8px;width:12px;height:12px;border:2px solid var(--orchid);border-radius:50%}
.intro .bullets{left:496px;top:112px;width:490px}
.vision{top:990px;height:362px;background:linear-gradient(90deg,#f4f2f8,#faf9fc)}
.vision .bullets{left:41px;top:80px;width:600px;z-index:2}
.baby-photo{left:660px;top:40px;width:384px;height:322px;z-index:1;background:radial-gradient(ellipse at 60% 45%,#f1d2c0 0%,#f7ebe4 45%,#f4f2f8 80%)}

.about{top:1352px;height:397px;background:linear-gradient(90deg,#4a1f47,#6a3a66 50%,#4a1f47);color:#eee;text-align:center}
.about h2{position:absolute;left:0;right:0;top:50px;color:#d98cc3;font-size:48px;font-weight:600}
.about-text{position:absolute;left:70px;right:70px;top:126px;font-size:14.5px;line-height:1.55}
.about-text p{margin-bottom:18px}
.btn-orchid{background:var(--orchid);color:var(--white);border-radius:3px;box-shadow:0 3px 0 var(--orchid-dark);display:flex;align-items:center;justify-content:center;font-size:22px}
.about .btn-orchid{left:419px;top:296px;width:204px;height:51px}

.newsletter{top:1749px;height:298px;background:var(--white);text-align:center}
.newsletter h2{position:absolute;left:0;right:0;top:50px;color:var(--orchid);font-size:44px;font-weight:600}
.newsletter p{position:absolute;left:250px;right:250px;top:128px;font-size:16px;line-height:1.6;color:#444}
.email{left:180px;top:197px;width:521px;height:51px;background:var(--blush);border:1px solid #e6dbe3;border-radius:3px;font-size:15px;color:#777;padding-left:14px;display:flex;align-items:center}
.newsletter .btn-orchid{left:708px;top:197px;width:155px;height:51px}

.service{top:2047px;width:522px;height:365px;color:#3b2a3a}
.service.pregnancy{left:78px;background:var(--orchid)}
.service.baby{left:600px;background:var(--lavender)}
.service h3{position:absolute;left:25px;top:50px;font-size:48px;font-weight:600;color:#111}
.service p{position:absolute;left:25px;right:25px;top:128px;font-size:14px;line-height:1.6}
.service .bullets{position:absolute;left:66px;top:190px;font-size:14px;line-height:1.5;color:#111}
.service .bullets li{margin-bottom:8px;padding-left:22px}
.service .bullets li::before{top:4px;width:11px;height:11px;border-color:#3b2a3a}
.service-mark{right:40px;top:40px;width:180px;height:290px;border-radius:90px;background:rgba(255,255,255,.08)}

/* footer */
.to-top{left:560px;top:2463px}
.copyright{left:0;width:1200px;top:2568px;text-align:center;font-size:16px;color:var(--lavender)}
.copyright .script{font-size:19px;color:var(--plum)}
.social{left:0;width:1200px;top:2599px;display:flex;justify-content:center;gap:18px}
.social span{width:54px;height:54px;border-radius:50%;background:#9a9a9a;border:3px solid #ddd}
.social span:first-child{background:var(--lavender)}
.footer-bar{left:0;top:2693px;width:1200px;height:18px;background:var(--lavender)}
.footer-notch{left:585px;top:2680px}
</style>
</head>
<body>

<header>
  <div class="abs hero">
    <div class="abs hero-photo" role="img" aria-label="Photo of a pregnant woman seated on a mat receiving a back massage from a therapist"></div>
    <svg class="abs hero-swoop" width="1200" height="674" viewBox="0 0 1200 674" aria-hidden="true">
      <path d="M380 0 C520 180 560 440 470 674 L0 674 L0 0 Z" fill="#3a1637" opacity=".55"/>
      <path d="M300 0 C460 200 470 460 380 674 L0 674 L0 0 Z" fill="#3a1637" opacity=".35"/>
    </svg>
    <div class="abs brand script"><span class="brand-dot"></span><br>Willow Cradle Pregnancy and Baby Massage</div>
    <nav>
      <ul class="abs nav">
        <li><a class="active" href="#">Home</a></li>
        <li><a href="#">About Me</a></li>
        <li><a href="#">Pregnancy Massage</a></li>
        <li><a href="#">Baby Massage</a></li>
        <li><a href="#">Pricing</a></li>
        <li><a href="#">Contact Us</a></li>
      </ul>
    </nav>
    <h1 class="abs hero-title script">Ensure that your pregnancy is<br>happy and health</h1>
    <a class="abs hero-btn script">Get Started Now</a>
  </div>
</header>

<main>
  <section class="abs panel intro">
    <div class="abs heart-photo" role="img" aria-label="Photo of twin newborns wrapped in a peach blanket inside a heart frame"></div>
    <ul class="abs bullets">
      <li>Willow Cradle Pregnancy and Baby Massage was launched in 2017, offering massage for pregnant women, and instruction of baby massage to parents, grandparents and carers.</li>
    </ul>
  </section>

  <section class="abs panel vision">
    <div class="abs baby-photo" role="img" aria-label="Photo of a baby peeking out from under a white towel"></div>
    <ul class="abs bullets">
      <li>My vision is to provide a professional massage service to pregnant mothers and babies that also benefits from my skills and experience as a midwife.</li>
      <li>My expectation is that after each session, my clients should leave feeling relaxed, calm, emotionally nurtured, soothed.</li>
      <li>At all times, I will take the utmost care of your privacy, safety and comfort in what is a very personal, intimate time in your life.</li>
    </ul>
  </section>

  <section class="abs panel about" role="region" aria-label="About Me">
    <h2 class="script">About Me</h2>
    <div class="about-text">
      <p>Maren is a Practitioner of Pregnancy Massage, and a Paediatric Massage Consultant. She completed her training with Bloom Prenatal Training Academy, and the Little Touch Infant Massage Institute. The LTIMI is endorsed by the Coastal Midwifery Council. The Southern Natural Therapies Guild, and accredited by the Federation of Remedial Therapists.</p>
      <p>Maren is also a Registered Nurse and Midwife. Most of her professional career has been as a midwife, which has included working in the community in the UK, providing ante natal care and classes, intra partum care, home births, and postnatal care in the home. Maren has also worked in the private and public maternity sectors in Perth.</p>
    </div>
    <a class="abs btn-orchid script">Learn More</a>
  </section>

  <section class="abs panel newsletter">
    <h2 class="script">Newsletter Subsription</h2>
    <p>Subscribe to our Newsletter and get tips &amp; information. Join Our amazing Pregnancy tracking tools &amp; Training to know much more</p>
    <div class="abs email">Email id</div>
    <a class="abs btn-orchid script">Subscribe</a>
  </section>

  <section class="abs service pregnancy">
    <div class="abs service-mark" aria-hidden="true"></div>
    <h3 class="script">Pregnancy Massage</h3>
    <p>Pregnancy massage is the prenatal use of massage therapy to support the physiological, structural and emotional wellbeing of both mother and baby.</p>
    <ul class="bullets">
      <li>Benefits of Pregnancy Massage</li>
      <li>Is Pregnancy Massage Safe?</li>
      <li>Pregnancy Massage Session Available</li>
    </ul>
  </section>

  <section class="abs service baby">
    <div class="abs service-mark" aria-hidden="true"></div>
    <h3 class="script">Baby Massage</h3>
    <p>This class teaches parents and carers the brief basics of Baby massage so they can get started at home.</p>
    <ul class="bullets">
      <li>Benefits of Baby Massage</li>
      <li>Introductory Baby Massage Course</li>
      <li>Baby Massage Session Available</li>
    </ul>
  </section>
</main>

<footer>
  <svg class="abs to-top" width="80" height="80" viewBox="0 0 80 80" aria-label="Back to top" role="img">
    <circle cx="40" cy="40" r="36" fill="none" stroke="#b7679f" stroke-width="4"/>
    <path d="M22 50 L40 30 L58 50 Z" fill="#b7679f"/>
  </svg>
  <div class="abs copyright">© <span class="script">Willow Cradle Pregnancy and Baby Massage</span> - 2017. All Rights Reserved.</div>
  <div class="abs social" aria-label="Social links"><span></span><span></span><span></span><span></span></div>
  <svg class="abs footer-notch" width="30" height="14" viewBox="0 0 30 14" aria-hidden="true"><path d="M0 14 L15 0 L30 14 Z" fill="#8c82bb"/></svg>
  <div class="abs footer-bar"></div>
</footer>

</body>
</html>
```